tallow-brook.com

We are a small dollar lending company that will revolutionize the industry. We will do this by being completely transparent, fee free, etc and an interest rate that normal people can afford to pay. Over 10X less than our competition. We only allow our members to pay bills " bills paid fast", within 72 hours. Payday loans typically charge from 390%-600% with a terrible payback structure. We charge 36%, period, with a payback structure over 12 months. Our site will be very simple and easy to use but elegant at the same time. We do not want the site to be too busy, less is more and easier. We will have; Home, The Story, Why tallowbrook.com, Are you eligible? Members, Clients. To become a member you have to be referred by a current client of tallowbrook.com. A lot of the busy stuff will be saved for the Members and Clients sections. The feel must be elegant, easy to use and very simple to understand. I am looking for the green, white and black combinations of colors, very similar to my logo that was designed by Fernquillo.

```html
<!DOCTYPE html>
<html lang="en">
<head>
<meta charset="utf-8">
<title>Tallowbrook — Small Dollar Lending</title>
<link href="https://fonts.googleapis.com/css2?family=Lato:wght@300;400;700&family=League+Gothic&family=Ubuntu:wght@500&display=swap" rel="stylesheet">
<style>
:root{
  --green:#8dc63f;
  --green-btn:#9dd35a;
  --green-dark:#6fa72c;
  --ink:#111;
  --bar:#333;
  --bar-line:#4a4a4a;
  --page:#e1e1e1;
  --white:#fff;
  --soft:#f0f0f0;
  --text:#444;
  --grey-icon:#b3b3b3;
}
*{margin:0;padding:0;box-sizing:border-box}
html,body{width:1200px;height:1183px;overflow:hidden}
body{font-family:"Lato",sans-serif;background:var(--page);color:var(--text);position:relative}

/* header */
.header{position:absolute;top:0;left:0;width:1200px;height:108px;background:var(--white)}
.brand{position:absolute;left:171px;top:26px;display:flex;align-items:center;gap:10px}
.brand-dot{width:50px;height:50px;border-radius:50%;background:var(--green)}
.brand-name{font-family:"Lato",sans-serif;font-weight:400;font-size:29px;color:var(--ink);letter-spacing:-.5px}
.social{position:absolute;right:173px;top:28px;display:flex;gap:4px}
.social span{width:27px;height:27px;background:var(--grey-icon);display:block}
.call{position:absolute;right:173px;top:64px;font-size:21px;font-weight:300;color:var(--green);white-space:nowrap}
.call b{color:var(--ink);font-weight:400}

/* nav */
.nav{position:absolute;top:108px;left:0;width:1200px;height:45px;background:var(--bar)}
.nav ul{list-style:none;display:flex;position:absolute;left:171px;width:856px;height:45px}
.nav li{flex:1;display:flex;align-items:center;justify-content:center;color:#fff;font-size:11px;letter-spacing:-.3px;border-right:1px solid var(--bar-line);white-space:nowrap}
.nav li.active{background:#111}

/* hero */
.hero-band{position:absolute;top:153px;left:0;width:1200px;height:333px;background:var(--green)}
.hero{position:absolute;top:153px;left:171px;width:856px;height:333px;background:radial-gradient(ellipse at 45% 50%,#3fae1c 0%,#1d5a0d 35%,#0b1e06 70%,#050a03 100%)}
.hero-panel{position:absolute;left:516px;top:22px;width:317px;height:291px;background:rgba(0,0,0,.88);padding:18px 14px 0 17px;overflow:hidden}
.hero-kicker{font-family:"League Gothic",sans-serif;color:var(--green);font-size:34px;line-height:30px}
.hero-title{font-family:"League Gothic",sans-serif;color:var(--green);font-size:40px;line-height:42px;letter-spacing:.2px;padding-bottom:4px;border-bottom:1px solid #ccc;width:287px;white-space:nowrap}
.checks{list-style:none;margin-top:4px}
.checks li{font-family:"Ubuntu",sans-serif;font-weight:500;color:#fff;font-size:20px;height:34.3px;display:flex;align-items:center;gap:7px;white-space:nowrap}
.checks svg{width:22px;height:20px;flex:none}

/* main */
.main{position:absolute;top:486px;left:171px;width:856px;height:617px;background:var(--white)}
.card{position:absolute;top:53px;width:246px;height:398px;background:var(--white);border:1px solid #ddd;box-shadow:0 1px 3px rgba(0,0,0,.12);text-align:center}
.card-top{height:106px;background:repeating-linear-gradient(45deg,#efefef 0 3px,#e9e9e9 3px 6px)}
.card h2{font-weight:300;font-size:21px;color:#333;padding-top:17px;letter-spacing:.2px}
.card-icon{position:absolute;left:73px;top:53px;width:100px;height:100px;border-radius:50%;background:var(--ink);display:flex;align-items:center;justify-content:center}
.card p{font-size:13px;line-height:20.6px;color:#444;padding:58px 12px 0}
.btn{position:absolute;left:48px;top:321px;width:147px;height:52px;background:var(--green-btn);border-bottom:3px solid var(--green-dark);border-radius:3px;font-size:14px;color:#3a5a1a;display:flex;align-items:center;justify-content:center}
.c1{left:29px}.c2{left:304px}.c3{left:579px}

.clients{position:absolute;left:0;top:502px;width:856px;height:115px;background:var(--soft)}
.clients h3{position:absolute;left:48px;top:10px;font-weight:400;font-size:17px;color:#444}
.clients ul{list-style:none;position:absolute;top:44px;left:40px;width:780px;display:flex;justify-content:space-between}
.clients li{font-size:15px;font-weight:700;color:#555;display:flex;align-items:center;gap:6px;white-space:nowrap}
.clients li i{width:10px;height:10px;background:#555;border-radius:50%;display:block}

/* footer */
.footer{position:absolute;top:1103px;left:0;width:1200px;height:80px;background:var(--bar);text-align:center}
.footer nav{padding-top:22px;font-size:12.5px;color:#fff;letter-spacing:-.1px}
.footer nav span{color:#999;margin:0 4px}
.footer small{display:block;margin-top:8px;font-size:12px;color:#bbb}
</style>
</head>
<body>
<header class="header">
  <div class="brand"><span class="brand-dot"></span><span class="brand-name">TALLOWBROOK</span></div>
  <div class="social" aria-label="Social links"><span></span><span></span><span></span><span></span></div>
  <div class="call">CALL US <b>123.456.7890</b></div>
</header>

<nav class="nav">
  <ul>
    <li class="active">HOME</li><li>THE STORY</li><li>WHY TALLOWBROOK.COM</li><li>ARE YOU ELIGIBLE?</li><li>MEMBERS</li><li>CLIENTS</li><li>CONTACT US</li>
  </ul>
</nav>

<div class="hero-band"></div>
<section class="hero" role="img" aria-label="Green glowing world map over rows of golden dollar signs">
  <div class="hero-panel">
    <div class="hero-kicker">we are a</div>
    <div class="hero-title">DOLLAR LENDING COMPANY</div>
    <ul class="checks">
      <li><svg viewBox="0 0 22 20"><path d="M2 11l6 6L20 3" fill="none" stroke="#fff" stroke-width="3.5"/></svg>Completely Transparent</li>
      <li><svg viewBox="0 0 22 20"><path d="M2 11l6 6L20 3" fill="none" stroke="#fff" stroke-width="3.5"/></svg>Fee Free Service</li>
      <li><svg viewBox="0 0 22 20"><path d="M2 11l6 6L20 3" fill="none" stroke="#fff" stroke-width="3.5"/></svg>Affordable Interest Rate</li>
      <li><svg viewBox="0 0 22 20"><path d="M2 11l6 6L20 3" fill="none" stroke="#fff" stroke-width="3.5"/></svg>Pay Bills within 72 hours &amp;</li>
      <li><svg viewBox="0 0 22 20"><path d="M2 11l6 6L20 3" fill="none" stroke="#fff" stroke-width="3.5"/></svg>Much more</li>
    </ul>
  </div>
</section>

<main class="main">
  <article class="card c1">
    <div class="card-top"><h2>THE STORY</h2></div>
    <div class="card-icon"><svg width="46" height="42" viewBox="0 0 46 42"><path d="M12 3h30l-8 34H4z" fill="#fff"/><path d="M4 37h30" stroke="#111" stroke-width="3"/><path d="M16 11h20M14 18h20" stroke="#111" stroke-width="3"/><path d="M4 37c0 3 2 4 4 4h26" fill="none" stroke="#fff" stroke-width="3"/></svg></div>
    <p>Small dollar loans are either too hard to get, take too long to process or just impossible to pay back. There are between 15mm-18mm people each year that require the use of small dollar loans, so you are not alone....</p>
    <div class="btn">KNOW MORE</div>
  </article>
  <article class="card c2">
    <div class="card-top"><h2>MEMBERS</h2></div>
    <div class="card-icon"><svg width="58" height="42" viewBox="0 0 58 42"><circle cx="20" cy="11" r="9" fill="#fff"/><circle cx="42" cy="15" r="7" fill="#fff"/><path d="M2 41c0-12 8-17 18-17s18 5 18 17z" fill="#fff"/><path d="M34 41c0-8 2-13 8-15 8 0 14 4 14 15z" fill="#fff"/></svg></div>
    <p>Lorem ipsum dolor sit amet, consectetur adipiscing elit. Sed quis nisi euismod, fermentum tellus a, lobortis quam. Vestibulum condimentum mi vitae diam tristique, egestas dignissim diam matti semper ut tortor.....</p>
    <div class="btn">KNOW MORE</div>
  </article>
  <article class="card c3">
    <div class="card-top"><h2>ARE YOU ELIGIBLE?</h2></div>
    <div class="card-icon"><svg width="40" height="36" viewBox="0 0 40 36"><rect x="2" y="6" width="28" height="28" fill="#fff"/><rect x="7" y="11" width="18" height="18" fill="#111"/><path d="M9 18l6 6L36 2" fill="none" stroke="#fff" stroke-width="5"/></svg></div>
    <p>Donec eleifend accumsan nisl, nec laoreet leo iaculis sit amet. Vivamus varius arcu eu sagittis aliquam. Vivamus accumsan cursus hendrerit. Vivamus eu magna rhoncus, consectetur metus ac, varius lacus. Donec ultricies, torto....</p>
    <div class="btn">KNOW MORE</div>
  </article>

  <section class="clients">
    <h3>Our Clients</h3>
    <ul>
      <li>Lumora</li>
      <li><i></i>Ostrel</li>
      <li>Creamvale</li>
      <li>Wavorin</li>
      <li><i></i>Corvant</li>
      <li>Harvest Table</li>
    </ul>
  </section>
</main>

<footer class="footer">
  <nav>HOME<span>/</span>THE STORY<span>/</span>WHY TALLOWBROOK.COM<span>/</span>ARE YOU ELIGIBLE?<span>/</span>MEMBERS<span>/</span>CLIENTS<span>/</span>CONTACT US</nav>
  <small>Copyright © 2014 tallowbrook.com. All rights reserved.</small>
</footer>
</body>
</html>
```